Estate Planning Law Firm opening new branch in Florida

I am an experienced estate planning attorney that recently relocated to Florida. Looking for a banner Ad to place on platforms such as HomeLane, Chatterbox and Picturely to create publicity for firm and new leads.

```html
<!DOCTYPE html>
<html lang="en">
<head>
<meta charset="utf-8">
<title>Serenova Law Firm – Estate &amp; Financial Planning Banner</title>
<link href="https://fonts.googleapis.com/css2?family=Figtree:wght@600;700;800&display=swap" rel="stylesheet">
<style>
  :root {
    --teal: #1b6b6e;
    --teal-text: #1d6f72;
    --navy: #2d3e50;
    --ink: #0c0c0c;
    --paper: #ffffff;
    --dot: #2d3e50;
  }
  * { margin: 0; padding: 0; box-sizing: border-box; }
  html, body { width: 1200px; height: 675px; overflow: hidden; background: var(--paper); }
  .banner {
    position: relative;
    width: 1200px;
    height: 675px;
    overflow: hidden;
    background: var(--paper);
    font-family: "Figtree", "Helvetica Neue", Arial, sans-serif;
  }
  .backdrop { position: absolute; inset: 0; width: 1200px; height: 675px; }
  .brand {
    position: absolute;
    left: 36px;
    top: 34px;
    display: flex;
    align-items: center;
    gap: 10px;
    color: var(--navy);
    font-weight: 800;
  }
  .brand-mark { width: 16px; height: 16px; background: var(--teal); }
  .brand-name { font-size: 28px; letter-spacing: 0.5px; line-height: 1; }
  .brand-name small { display: block; font-size: 11px; letter-spacing: 1.5px; margin-top: 4px; font-weight: 800; }
  .eyebrow {
    position: absolute;
    left: 114px;
    top: 174px;
    color: var(--teal-text);
    font-size: 24px;
    font-weight: 700;
    letter-spacing: 0.2px;
  }
  .headline {
    position: absolute;
    left: 110px;
    top: 224px;
    color: var(--ink);
    font-size: 52px;
    font-weight: 800;
    line-height: 59px;
    letter-spacing: 0.3px;
  }
  .lede {
    position: absolute;
    left: 106px;
    top: 418px;
    width: 470px;
    color: var(--ink);
    font-size: 16.5px;
    font-weight: 700;
    line-height: 26.5px;
  }
</style>
</head>
<body>
<main class="banner">
  <svg class="backdrop" viewBox="0 0 1920 1080" aria-hidden="false">
    <defs>
      <radialGradient id="dial-tone" cx="0.45" cy="0.55" r="0.7">
        <stop offset="0" stop-color="#f4f7f8"/>
        <stop offset="0.55" stop-color="#e6eef1"/>
        <stop offset="0.85" stop-color="#9fc3cf"/>
        <stop offset="1" stop-color="#2a6f86"/>
      </radialGradient>
      <pattern id="dot-grid" width="24" height="24" patternUnits="userSpaceOnUse">
        <circle cx="4" cy="4" r="2.4" fill="var(--dot)"/>
      </pattern>
    </defs>
    <path class="corner-navy" d="M1575 0 C1570 60 1640 70 1700 100 C1760 130 1745 190 1745 235 L1920 235 L1920 0 Z" fill="#2d3e50"/>
    <rect class="tab-teal" x="-20" y="196" width="142" height="92" rx="10" fill="#1b6b6e"/>
    <rect x="0" y="238" width="54" height="300" fill="url(#dot-grid)"/>
    <rect x="1122" y="312" width="78" height="300" fill="url(#dot-grid)"/>
    <path class="wave-teal" d="M0 505 C70 520 130 570 135 650 C140 760 150 860 260 895 C340 920 420 905 480 940 C550 980 575 1040 578 1080 L0 1080 Z" fill="#1b6b6e"/>
    <rect class="bar-navy" x="960" y="968" width="360" height="94" rx="8" fill="#2d3e50"/>
    <ellipse role="img" aria-label="Photo: close-up of a compass dial with a steel needle pointing toward the word retirement" cx="1975" cy="720" rx="850" ry="490" fill="url(#dial-tone)"/>
  </svg>

  <div class="brand">
    <span class="brand-mark"></span>
    <span class="brand-name">SERENOVA<small>LAW FIRM, PLLC</small></span>
  </div>

  <p class="eyebrow">WELCOME TO SERENOVA</p>

  <h1 class="headline">ESTATE PLANNING<br>&amp; FINANCIAL PLANNING<br>UNDER ONE ROOF</h1>

  <p class="lede">ESTATE PLANNING AND FINANCIAL PLANNING ISN’T JUST FOR THE ULTRA-WEALTHY. WE’RE HERE TO HELP FAMILIES PLAN FOR THEIR LEGACY AND PROTECT THEIR WEALTH</p>
</main>
</body>
</html>
```